Telecommunications/Power civil contractor needs business card design

Were a new telecommunications/power underground civil contractor that is looking for a new business card design. Our company colours are silver or grey and orange. Feel free to use the white background logo or the black background logo.

Target Market(s)

Local contractors, utility companies, private sector mining/energy companies, developers.

Industry/Entity Type

Telecommunications

Contact Information for Business Card

Each card will need the following info:
Persons name:
Title:
E-mail:
Phone number:
Shop Address:
Mailing Address:

Requirements
Must have
• Each card will need the following info:
• Persons name:
• Title:
• E-mail:
• Phone number:
• Shop Address:
• Mailing Address:

```html
<!DOCTYPE html>
<html lang="en">
<head>
<meta charset="utf-8">
<title>Ridgeway Conduit Inc — Business Card</title>
<link rel="stylesheet" href="https://fonts.googleapis.com/css2?family=Source+Sans+3:wght@400;600;700&display=swap">
<style>
  :root {
    --orange: #f05a22;
    --grey: #6d6e70;
    --grey-light: #9a9b9d;
    --ink: #4a4a4c;
    --card-white: #ffffff;
    --card-black: #161616;
    --backdrop: #d9dce3;
  }
  * { box-sizing: border-box; margin: 0; padding: 0; }
  html, body {
    width: 1200px; height: 797px; overflow: hidden;
    background: var(--backdrop);
    font-family: "Source Sans 3", Arial, sans-serif;
  }
  .stage {
    position: relative; width: 1200px; height: 797px;
    display: flex; align-items: center; justify-content: center; gap: 60px;
  }
  .card {
    position: relative; width: 520px; height: 297px; overflow: hidden;
    box-shadow: 0 10px 24px rgba(0,0,0,0.18);
  }
  .card-front { background: var(--card-white); }
  .card-back { background: var(--card-black); display: flex; align-items: center; justify-content: center; }

  .brand {
    position: absolute; left: 28px; top: 58px; width: 160px;
    display: flex; flex-direction: column; align-items: center; gap: 10px;
  }
  .brand-dot {
    width: 54px; height: 54px; border-radius: 50%;
    border: 4px solid var(--grey-light);
  }
  .brand-name {
    color: var(--orange); font-weight: 700; font-size: 17px;
    text-align: center; line-height: 1.05; letter-spacing: 0.5px; text-transform: uppercase;
  }

  .divider {
    position: absolute; left: 206px; top: 46px; width: 1px; height: 118px;
    background: var(--grey);
  }

  .contact { position: absolute; left: 222px; top: 44px; color: var(--ink); }
  .contact-name { color: var(--orange); font-weight: 700; font-size: 16px; line-height: 1.1; }
  .contact-title { font-size: 15px; color: var(--grey); line-height: 1.2; margin-bottom: 8px; }
  .contact-address { font-size: 12px; line-height: 1.35; color: var(--grey); margin-bottom: 8px; }
  .contact-line { display: flex; align-items: center; gap: 8px; font-size: 12px; color: var(--grey); line-height: 1.5; }
  .contact-icon { width: 12px; height: 12px; flex: none; }

  .swoosh { position: absolute; left: 0; bottom: 0; width: 520px; height: 297px; }

  .back-mark { display: flex; align-items: center; gap: 14px; }
  .back-dot {
    width: 72px; height: 72px; border-radius: 50%;
    border: 5px solid var(--grey-light);
  }
  .back-name {
    color: var(--grey-light); font-weight: 700; font-size: 22px; line-height: 1.05;
    letter-spacing: 0.6px; text-transform: uppercase;
  }
</style>
</head>
<body>
<main class="stage">
  <section class="card card-front" aria-label="Business card front">
    <div class="brand">
      <span class="brand-dot"></span>
      <span class="brand-name">Ridgeway<br>Conduit Inc</span>
    </div>
    <span class="divider"></span>
    <div class="contact">
      <p class="contact-name">Dana Holt</p>
      <p class="contact-title">Managing Director</p>
      <p class="contact-address">N. 48 Quarry Road,<br>Suite 210, Kellan, WA 99021</p>
      <p class="contact-line">
        <svg class="contact-icon" viewBox="0 0 12 12" aria-hidden="true"><circle cx="6" cy="6" r="6" fill="var(--orange)"/><path d="M3.6 3.2 l1.3 0 l0.5 1.5 l-0.8 0.6 a4 4 0 0 0 2 2 l0.6 -0.8 l1.5 0.5 l0 1.3 a5.5 5.5 0 0 1 -5.1 -5.1z" fill="#fff"/></svg>
        509.555.0142
      </p>
      <p class="contact-line">
        <svg class="contact-icon" viewBox="0 0 12 12" aria-hidden="true"><circle cx="6" cy="6" r="6" fill="var(--orange)"/><rect x="3" y="4" width="6" height="4.2" fill="none" stroke="#fff" stroke-width="0.9"/><path d="M3 4 L6 6.4 L9 4" fill="none" stroke="#fff" stroke-width="0.9"/></svg>
        info@ridgewayconduit.com
      </p>
    </div>
    <svg class="swoosh" viewBox="0 0 520 297" aria-hidden="true">
      <path d="M0 232 C150 222 330 205 520 150 L520 160 C340 222 170 245 0 250 Z" fill="var(--grey)"/>
      <path d="M0 250 C180 244 360 222 520 160 L520 297 L0 297 Z" fill="var(--orange)"/>
      <path d="M140 262 C300 250 430 215 520 175 L520 190 C420 232 290 258 140 262 Z" fill="var(--card-white)"/>
      <path d="M0 268 C120 266 170 264 140 262 C100 262 40 264 0 264 Z" fill="var(--card-white)"/>
    </svg>
  </section>

  <section class="card card-back" aria-label="Business card back">
    <div class="back-mark">
      <span class="back-dot"></span>
      <span class="back-name">Ridgeway<br>Conduit Inc</span>
    </div>
  </section>
</main>
</body>
</html>
```